Business Card Design for Retail Product Line

We need a two-sided, full-color business card for a new oral care product line. The feel of the card should invoke emotions of happiness and health. It should be bright, cheerful and modern in appearance. The card should be mostly matte finish, but with elements of spot-gloss and/or raised/embossed features (print, logo, tag lines, etc.).

Target Market(s)

People who are into whole-body health, eat well and understand the importance of nutrition.

Industry/Entity Type

Health And Wellness

Contact Information for Business Card

The logo, color scheme and tag-lines have all been developed and artwork is attached. Card is to be standard-sized and should use a mix of clean, sans-serif fonts; the main font (DIN) is attached as well. The card will be used for 3 individuals and should include placeholders for:
1. Name
2. Title (for example, "CEO")
3. Business address
4. Phone number
5. Website
6. Email address

Font styles to use
Sans Serif
Other font styles liked:
• DIN font

Colors
faa54b
000000
5c5c5c
a2ce44

Requirements
Must have
• 2 sides
• Full color orange on one side
• Image of DNA leaves
• Tag line "Shine from the Roots Up", on single side with orange background
• Company Logo (Plure) on same side as text (name, phone, address, etc.)
• Name, Title, Business Address, Phone Number, Website, Email address
• UPDATE: "Brisk Meadow", not "Brisk M Eadow"
Should not have
• Calligraphy
• Dark colors
• UPDATE!! Do not include "Turmeric infused toothpaste" on the business card
• UPDATE #2!! Do not include "Brisk Meadow" on the business card

```html
<!DOCTYPE html>
<html lang="en">
<head>
<meta charset="UTF-8">
<title>Plure Business Card</title>
<link rel="stylesheet" href="https://fonts.googleapis.com/css2?family=Open+Sans:wght@400;600;700&family=Barlow:wght@500;700&display=swap">
<style>
  :root {
    --orange-top: #f2c93f;
    --orange-bottom: #e79a2e;
    --orange-logo: #e9a232;
    --white: #ffffff;
    --leaf-green: #8cc63f;
    --leaf-dark: #3aa03a;
    --helix-grey: #c9cbcc;
    --backdrop: #efeeec;
  }
  * { margin: 0; padding: 0; box-sizing: border-box; }
  html, body { width: 1200px; height: 900px; overflow: hidden; }
  body { background: var(--backdrop); position: relative; font-family: "Open Sans", sans-serif; }

  .card { position: absolute; overflow: hidden; box-shadow: 0 6px 18px rgba(0,0,0,0.12); }

  /* Front side */
  .card-front { left: 78px; top: 34px; width: 587px; height: 364px; background: var(--white); display: flex; }
  .contact-panel {
    width: 294px; height: 100%;
    background: linear-gradient(180deg, var(--orange-top) 0%, var(--orange-bottom) 100%);
    color: var(--white); padding: 90px 0 0 31px;
  }
  .contact-name { font-weight: 700; font-size: 18px; line-height: 1.2; }
  .contact-title { font-size: 14.5px; line-height: 1.3; margin-bottom: 15px; }
  .contact-address { font-size: 14.5px; line-height: 1.45; margin-bottom: 13px; }
  .contact-list { list-style: none; font-size: 14.5px; line-height: 1.45; }
  .contact-list li { display: flex; align-items: center; gap: 8px; }
  .contact-list svg { width: 12px; height: 12px; fill: var(--white); flex: none; }
  .logo-panel { flex: 1; display: flex; align-items: center; justify-content: center; }
  .brand-name { font-family: "Open Sans", sans-serif; font-weight: 700; font-size: 76px; color: var(--orange-logo); letter-spacing: -1px; }

  /* Back side */
  .card-back {
    left: 388px; top: 505px; width: 567px; height: 352px;
    background: linear-gradient(180deg, var(--orange-top) 0%, var(--orange-bottom) 100%);
  }
  .brand-watermark {
    position: absolute; left: 175px; top: -20px;
    font-family: "Open Sans", sans-serif; font-weight: 700; font-size: 150px;
    color: var(--white); opacity: 0.14; letter-spacing: -3px;
  }
  .dna-leaves-art {
    position: absolute; left: 0; top: 0; width: 255px; height: 100%;
    background: linear-gradient(170deg, var(--white) 0%, var(--leaf-green) 35%, var(--leaf-dark) 60%, var(--helix-grey) 100%);
    clip-path: polygon(0 0, 62% 0, 100% 40%, 78% 100%, 0 100%);
  }
  .tagline {
    position: absolute; left: 286px; top: 150px;
    font-family: "Barlow", sans-serif; color: var(--white);
  }
  .tagline-lead { font-weight: 700; font-size: 74px; line-height: 0.9; letter-spacing: -1px; }
  .tagline-rest { font-weight: 700; font-size: 42px; line-height: 1.15; margin-top: 8px; }
</style>
</head>
<body>
  <section class="card card-front" aria-label="Business card front">
    <div class="contact-panel">
      <p class="contact-name">Daniel Harper</p>
      <p class="contact-title">Managing Director</p>
      <p class="contact-address">12345, Address Goes Here<br>Country Name, 123456.</p>
      <ul class="contact-list">
        <li><svg viewBox="0 0 24 24"><path d="M6.6 10.8a15.1 15.1 0 0 0 6.6 6.6l2.2-2.2a1 1 0 0 1 1-.25 11.4 11.4 0 0 0 3.6.57 1 1 0 0 1 1 1V20a1 1 0 0 1-1 1A17 17 0 0 1 3 4a1 1 0 0 1 1-1h3.5a1 1 0 0 1 1 1c0 1.25.2 2.450.57 3.57a1 1 0 0 1-.25 1z"/></svg>044-123 456 789</li>
        <li><svg viewBox="0 0 24 24"><path d="M2 5h20v14H2z M2 5l10 8 10-8" /></svg>info@webname.com</li>
        <li><svg viewBox="0 0 24 24"><circle cx="12" cy="12" r="10"/></svg>www.websitename.com</li>
      </ul>
    </div>
    <div class="logo-panel">
      <span class="brand-name">Plure</span>
    </div>
  </section>

  <section class="card card-back" aria-label="Business card back">
    <span class="brand-watermark" aria-hidden="true">Plure</span>
    <div class="dna-leaves-art" role="img" aria-label="Illustration of green leaves growing from a grey DNA helix"></div>
    <div class="tagline">
      <p class="tagline-lead">shine</p>
      <p class="tagline-rest">FROM THE<br>ROOTS UP</p>
    </div>
  </section>
</body>
</html>
```